HearthMile business card and stationary design

We are looking for a simple yet elegant design for our mortgage company business card and stationary.

The card should include:
Name (Marcus Pell)
Title (CEO)
Phone Number (419-770-0182)
Address (48 Birchwell Court, Suite 314, Larkmoor, OH 44190)
Email (email@hearthmile.example)
"NMLS" i.e. (NMLS 61947)
"Company NMLS" (Company NMLS 274615)

Contact Information for Business Card

See above

```html
<!DOCTYPE html>
<html lang="en">
<head>
<meta charset="utf-8">
<title>HearthMile Business Card</title>
<link rel="stylesheet" href="https://fonts.googleapis.com/css2?family=Inter:wght@400;600;700&family=Montserrat:wght@500&display=swap">
<style>
  :root {
    --bg: #d9dadc;
    --card-white: #ffffff;
    --brand-blue: #0aa6e8;
    --back-blue: #02aeee;
    --back-ink: #1a63de;
    --ink: #1b2533;
    --navy: #152234;
    --muted: #2a2f38;
  }
  * { margin: 0; padding: 0; box-sizing: border-box; }
  html, body {
    width: 1200px; height: 800px; overflow: hidden;
    background: var(--bg);
    font-family: "Inter", Arial, sans-serif;
  }
  .stage {
    width: 1200px; height: 800px;
    display: flex; align-items: center; justify-content: center; gap: 40px;
  }
  .card {
    position: relative;
    width: 540px; height: 309px;
    border-radius: 22px;
    overflow: hidden;
    box-shadow: 0 10px 26px rgba(0,0,0,0.18);
  }
  .card-front { background: var(--card-white); }
  .card-back { background: var(--back-blue); display: flex; align-items: center; justify-content: center; }

  .edge-tab {
    position: absolute; right: 0; top: 48px;
    width: 7px; height: 26px; background: var(--brand-blue);
  }
  .edge-band {
    position: absolute; left: 0; bottom: 34px;
    width: 7px; height: 110px; background: var(--navy);
  }

  .wordmark {
    font-family: "Montserrat", Arial, sans-serif;
    font-weight: 500;
    letter-spacing: 0.5px;
    white-space: nowrap;
  }
  .front-wordmark {
    position: absolute; left: 46px; top: 96px;
    font-size: 42px; line-height: 52px; color: var(--brand-blue);
  }
  .back-wordmark { font-size: 62px; color: var(--back-ink); }

  .identity {
    position: absolute; right: 46px; top: 70px;
    text-align: right;
  }
  .identity .person-name { font-size: 20px; font-weight: 700; color: var(--ink); }
  .identity .person-title { font-size: 14px; font-weight: 400; color: var(--brand-blue); margin-top: 2px; letter-spacing: 1px; }

  .contact-list {
    position: absolute; left: 58px; top: 166px;
    list-style: none; font-size: 13px; line-height: 17px; color: var(--muted);
  }
  .contact-list li { display: flex; align-items: flex-start; gap: 8px; }
  .contact-list svg { width: 10px; height: 10px; margin-top: 4px; flex: none; fill: var(--brand-blue); }
  .licenses { margin-top: 8px; padding-left: 18px; }
</style>
</head>
<body>
<main class="stage">
  <section class="card card-front" aria-label="Business card front">
    <span class="edge-tab"></span>
    <span class="edge-band"></span>
    <div class="wordmark front-wordmark">HearthMile</div>
    <div class="identity">
      <div class="person-name">Marcus Pell</div>
      <div class="person-title">CEO</div>
    </div>
    <ul class="contact-list">
      <li>
        <svg viewBox="0 0 10 10"><path d="M5 0a3.6 3.6 0 0 0-3.6 3.6C1.4 6.3 5 10 5 10s3.6-3.7 3.6-6.4A3.6 3.6 0 0 0 5 0zm0 5a1.4 1.4 0 1 1 0-2.8A1.4 1.4 0 0 1 5 5z"/></svg>
        <span>48 Birchwell Court, Suite 314<br>Larkmoor, OH 44190</span>
      </li>
      <li>
        <svg viewBox="0 0 10 10"><path d="M2 0.5l1.8 2.2-1 1.2a6 6 0 0 0 3.3 3.3l1.2-1 2.2 1.8-1 1.6C4.6 9.8 0.2 5.4 0.4 1.5z"/></svg>
        <span>419-770-0182</span>
      </li>
      <li>
        <svg viewBox="0 0 10 10"><path d="M0 2h10v6H0z M0 2l5 3.4L10 2" stroke="#fff" stroke-width="0.8"/></svg>
        <span>info@hearthmile.example</span>
      </li>
      <li>
        <svg viewBox="0 0 10 10"><circle cx="5" cy="5" r="5"/></svg>
        <span>hearthmile.example</span>
      </li>
      <li class="licenses"><span>Company NMLS 274615<br>NMLS 61947</span></li>
    </ul>
  </section>

  <section class="card card-back" aria-label="Business card back">
    <div class="wordmark back-wordmark">HearthMile</div>
  </section>
</main>
</body>
</html>
```